Ferncrest Roam Wording For Logo & Business card

I have the logo, I just need the "Ferncrest Roam" wording to go with it, and a business card design. The only thing on the business card is the website info. We provide nature connection experiences, and bolster these efforts through writing and host a platform for community around it.

I also have an idea of what it could look like (sketch), though I'm really not sure how it would come out. I am open to the best design and happy to consider original artwork. You can see what the site is about at FerncrestRoam.example.

Contact Information for Business Card

The only thing on the business card is the website info and the design. I will put other messaging on the back.

Website lettering (FerncrestRoam.example) in Montserrat

Logo Text

Ferncrest Roam (letters optional)

Font styles to use
Other font styles liked:
• montserrat

```html
<!DOCTYPE html>
<html lang="en">
<head>
<meta charset="utf-8">
<title>Ferncrest Roam — Business Card</title>
<link rel="stylesheet" href="https://fonts.googleapis.com/css2?family=Montserrat:wght@500;700&display=swap">
<style>
  :root {
    --backdrop: #e9e9e7;
    --card-white: #f7f7f6;
    --navy: #160726;
    --emblem: #2c1348;
    --flame-red: #d8340a;
    --sun-yellow: #ffd200;
    --amber: #ef8a06;
    --ember: #b82406;
    --ink: #1c1c1c;
    --white: #ffffff;
  }
  * { box-sizing: border-box; margin: 0; padding: 0; }
  html, body { width: 1200px; height: 801px; overflow: hidden; }
  body {
    background: var(--backdrop);
    display: flex;
    align-items: center;
    justify-content: center;
    gap: 40px;
  }
  .card {
    position: relative;
    width: 540px;
    height: 309px;
    overflow: hidden;
    box-shadow: 0 6px 18px rgba(0,0,0,.18);
  }
  /* Front */
  .card--front { background: var(--card-white); }
  .brand {
    position: absolute;
    left: 24px; top: 22px;
    display: flex; align-items: center; gap: 18px;
  }
  .brand__dot {
    width: 96px; height: 96px; border-radius: 50%;
    background: var(--emblem);
    flex: none;
  }
  .brand__name {
    font-family: "Montserrat", sans-serif;
    font-weight: 700;
    font-size: 30px;
    letter-spacing: 1px;
    text-transform: uppercase;
    color: var(--navy);
    line-height: 1.05;
    white-space: nowrap;
  }
  .navy-band {
    position: absolute;
    left: 0; top: 136px;
    width: 430px; height: 30px;
    background: var(--navy);
  }
  .accent-band {
    position: absolute;
    right: 0; top: 118px;
    width: 78px; height: 28px;
    background: var(--flame-red);
  }
  .website {
    position: absolute;
    left: 100px; top: 214px;
    display: flex; align-items: center; gap: 10px;
    font-family: "Montserrat", sans-serif;
    font-weight: 500;
    font-size: 17px;
    color: var(--ink);
    white-space: nowrap;
  }
  .website svg { width: 16px; height: 16px; flex: none; }
  .website svg circle { fill: none; stroke: var(--flame-red); stroke-width: 2; }
  .website svg path { fill: none; stroke: var(--flame-red); stroke-width: 1.6; }
  /* Back */
  .card--back {
    background: radial-gradient(ellipse 60% 75% at 48% 48%, var(--sun-yellow) 0%, var(--amber) 45%, var(--flame-red) 75%, var(--ember) 100%);
    display: flex; flex-direction: column; align-items: center; justify-content: center; gap: 18px;
  }
  .card--back .brand__dot { width: 130px; height: 130px; }
  .card--back .brand__name { color: var(--white); font-size: 32px; }
</style>
</head>
<body>
  <section class="card card--front" aria-label="Business card front">
    <div class="brand">
      <span class="brand__dot"></span>
      <span class="brand__name">Ferncrest Roam</span>
    </div>
    <div class="accent-band"></div>
    <div class="navy-band"></div>
    <p class="website">
      <svg viewBox="0 0 24 24" aria-hidden="true"><circle cx="12" cy="12" r="10"/><path d="M2 12h20M12 2c3 3 3 17 0 20M12 2c-3 3-3 17 0 20"/></svg>
      www.ferncrestroam.example
    </p>
  </section>

  <section class="card card--back" aria-label="Business card back">
    <span class="brand__dot"></span>
    <span class="brand__name">Ferncrest Roam</span>
  </section>
</body>
</html>
```